Bright Harbor Counseling Letterhead for hip modern business

I would like some ombre use of the colors in the logo hip letterhead that incorporates logo colors and feel, needs to connect with young professionals and college students. i need to be able to write letters to schools to excuse absences as well. i like color blocks on one side preferably using colors from the attached logo design.

Target Market(s)

high income young people, young adults and college students

Industry/Entity Type

mental health

Font styles to use
Serif
Sans Serif

Colors
0054AA
0677BA
7BADD7
CADEEF
E8F1F8
0094D4
00A9DD
6FCCEA
C7EBF8
E9F6FB
00AB8E
00BBA5
67D7C9
C6EFE9
E9F9F6
59FF00
82FF00
B8FF75
E3FFCB
F4FFEA
A7469A
B969AE
D3A5CF
EDDBEB
F8F0F9
6B429C
8869AF
B7A5CE
E3DAEB
F3F0F8

Requirements
Must have
• a modern hip feel, somewhat color

```html
<!DOCTYPE html>
<html lang="en">
<head>
<meta charset="utf-8">
<title>Bright Harbor Counseling — Letterhead</title>
<link rel="stylesheet" href="https://fonts.googleapis.com/css2?family=Open+Sans:wght@300;400;600&display=swap">
<style>
  :root {
    --stage: #333333;
    --paper: #ffffff;
    --ink: #4a4a4a;
    --ink-soft: #6e6e6e;
    --ink-dark: #2e2e2e;
    --blue: #0677BA;
    --sky: #00A9DD;
    --teal: #00BBA5;
    --plum: #A7469A;
    --violet: #6B429C;
  }
  * { box-sizing: border-box; margin: 0; padding: 0; }
  html, body {
    width: 1200px; height: 962px; overflow: hidden;
    background: var(--stage);
    font-family: "Open Sans", Arial, sans-serif;
    color: var(--ink);
  }
  .letterhead {
    position: absolute; left: 282px; top: 36px;
    width: 636px; height: 890px;
    background: var(--paper);
    box-shadow: 0 6px 24px rgba(0,0,0,.35);
  }
  .brand {
    position: absolute; right: 56px; top: 50px;
    display: flex; align-items: center; gap: 10px;
  }
  .brand-dot { width: 14px; height: 14px; border-radius: 50%; background: var(--violet); }
  .brand-name { font-weight: 300; font-size: 22px; color: var(--ink-dark); letter-spacing: .2px; }

  .letter {
    position: absolute; left: 66px; top: 190px; width: 380px;
    font-size: 11.5px; line-height: 1.45;
  }
  .date { margin-bottom: 12px; }
  .recipient { margin-bottom: 14px; }
  .salutation { font-weight: 600; color: var(--ink-dark); margin-bottom: 12px; }
  .letter p.body { margin-bottom: 12px; color: var(--ink-soft); }

  .closing {
    position: absolute; left: 470px; top: 370px; width: 120px;
    font-size: 11.5px; line-height: 1.45; color: var(--ink-soft);
  }
  .signature {
    display: block; width: 100px; height: 26px; margin: 8px 0;
    background: linear-gradient(90deg, #ececec, #dcdcdc);
    border-radius: 4px;
  }

  .accent-block {
    position: absolute; left: 66px; bottom: 48px;
    width: 96px; height: 96px; border-radius: 12px;
    background: linear-gradient(135deg, var(--sky) 0%, var(--blue) 35%, var(--violet) 70%, var(--plum) 100%);
    opacity: .85;
  }
  .footer {
    position: absolute; right: 56px; bottom: 52px;
    text-align: right; font-size: 10px; line-height: 1.6; color: var(--ink-dark);
  }
  .footer-name { font-weight: 600; }
  .contacts {
    display: flex; gap: 4px 10px; justify-content: flex-end; align-items: center;
    flex-wrap: wrap; max-width: 390px; margin-left: auto;
  }
  .contact { display: inline-flex; align-items: center; gap: 4px; }
  .contact svg { width: 10px; height: 10px; }
</style>
</head>
<body>
<main class="letterhead">
  <header class="brand">
    <span class="brand-dot"></span>
    <span class="brand-name">Bright Harbor Counseling</span>
  </header>

  <section class="letter">
    <p class="date">January 12, 2014</p>
    <p class="recipient">Mr. Alan Reed<br>President<br>Northfield College<br>111 Street Name, Suite#<br>City, State, 12345</p>
    <p class="salutation">Dear Mr. Reed,</p>
    <p class="body">Lorem Ipsum is simply dummy text of the printing and typesetting industry. Lorem Ipsum has been the industry’s standard dummy text ever since the 1500s, when an unknown printer took a galley of type and scrambled it to make a type specimen book. It has survived not only five centuries, but also the leap into electronic typesetting, remaining essentially unchanged.</p>
    <p class="body">The standard chunk of Lorem Ipsum used since the 1500s is reproduced below for those interested. Sections 1.10.32 and 1.10.33 from “de Finibus Bonorum et Malorum” by Cicero are also reproduced in their exact original form, accompanied by English versions from the 1914 translation by H. Rackham.</p>
    <p class="body">Lorem Ipsum is simply dummy text of the printing and typesetting industry. Lorem Ipsum has been the industry’s standard dummy text ever since the 1500s, when an unknown printer took a galley of type and scrambled it to make a type specimen book. It has survived not only five centuries, but also the leap into electronic typesetting, remaining essentially unchanged. It was popularised in the</p>
  </section>

  <section class="closing">
    <p>Sincerely Yours,</p>
    <span class="signature" role="img" aria-label="Handwritten signature"></span>
    <p>Name Last Name<br>Company Name</p>
  </section>

  <div class="accent-block" role="img" aria-label="Colour accent block in brand blues and purples"></div>

  <footer class="footer">
    <p class="footer-name">Bright Harbor Counseling</p>
    <p>Suite 210 Harbor Lane, State, Zip 4019, Country</p>
    <div class="contacts">
      <span class="contact"><svg viewBox="0 0 10 10"><circle cx="5" cy="5" r="5" fill="var(--teal)"/><path d="M3 2.6l1 .2.4 1.2-.6.5a3.5 3.5 0 0 0 1.7 1.7l.5-.6 1.2.4.2 1a4.8 4.8 0 0 1-4.4-4.4z" fill="#fff"/></svg>(00) 05550 142 310</span>
      <span class="contact"><svg viewBox="0 0 10 10"><circle cx="5" cy="5" r="5" fill="var(--blue)"/><rect x="2.8" y="3" width="4.4" height="4" fill="#fff"/></svg>(00) 05550 142 311</span>
      <span class="contact"><svg viewBox="0 0 10 10"><circle cx="5" cy="5" r="5" fill="var(--plum)"/><path d="M2.5 3.3h5v3.4h-5zM2.5 3.3L5 5.2l2.5-1.9" fill="none" stroke="#fff" stroke-width=".8"/></svg>hello@brightharborcare.com</span>
      <span class="contact"><svg viewBox="0 0 10 10"><circle cx="5" cy="5" r="5" fill="var(--sky)"/><circle cx="5" cy="5" r="2.4" fill="none" stroke="#fff" stroke-width=".8"/></svg>www.brightharborcare.com</span>
    </div>
  </footer>
</main>
</body>
</html>
```